Corbell Lending Partners - Real estate loans - need a business card with a logo

I need a logo and a business card that looks elegant - that looks as if it is a big stablish corporation - We do real estate loans, my goal is to brand myself with colors black background - gold or silver letters - some combination - Name of the company different color than the rest of the card -

```html
<!DOCTYPE html>
<html lang="en">
<head>
<meta charset="UTF-8">
<title>Corbell Lending Partners – Business Card</title>
<link rel="stylesheet" href="https://fonts.googleapis.com/css2?family=Arimo:wght@400;700&family=Oswald:wght@500&display=swap">
<style>
  :root {
    --backdrop: #141414;
    --card: #232323;
    --card-edge: #2c2c2c;
    --silver: #c9c9c9;
    --silver-soft: #a9a9a9;
    --rule: #8c8c8c;
  }
  * { margin: 0; padding: 0; box-sizing: border-box; }
  html, body { width: 1200px; height: 900px; overflow: hidden; }
  body {
    background: var(--backdrop);
    font-family: "Arimo", Arial, sans-serif;
    position: relative;
  }
  .card {
    position: absolute;
    left: 285px;
    width: 630px;
    height: 360px;
    background: linear-gradient(135deg, var(--card) 0%, #1e1e1e 55%, var(--card-edge) 100%);
    box-shadow: 0 18px 40px rgba(0,0,0,0.6);
  }
  .card--front { top: 70px; }
  .card--back { top: 470px; }

  .brand {
    position: absolute;
    inset: 0;
    display: flex;
    flex-direction: column;
    align-items: center;
    justify-content: center;
    gap: 22px;
  }
  .brand__mark {
    width: 64px;
    height: 64px;
    background: var(--silver);
  }
  .brand__name {
    font-family: "Arimo", Arial, sans-serif;
    font-weight: 700;
    font-size: 34px;
    letter-spacing: 2px;
    text-transform: uppercase;
    color: var(--silver);
  }

  .person {
    position: absolute;
    right: 340px;
    top: 135px;
    text-align: right;
  }
  .person__name {
    font-family: "Oswald", "Arial Narrow", sans-serif;
    font-weight: 500;
    font-size: 36px;
    letter-spacing: 1px;
    text-transform: uppercase;
    color: var(--silver-soft);
    line-height: 1.1;
  }
  .person__role {
    font-size: 17px;
    color: var(--silver-soft);
    margin-top: 2px;
  }
  .divider {
    position: absolute;
    left: 312px;
    top: 120px;
    width: 2px;
    height: 120px;
    background: var(--rule);
  }
  .contact {
    position: absolute;
    left: 340px;
    top: 118px;
    list-style: none;
    color: var(--silver);
    font-size: 18px;
    line-height: 25px;
  }
  .contact__item { display: flex; align-items: center; gap: 6px; }
  .contact__icon { width: 13px; height: 13px; flex: none; }
</style>
</head>
<body>
  <section class="card card--front">
    <div class="brand">
      <div class="brand__mark"></div>
      <div class="brand__name">Corbell Lending Partners</div>
    </div>
  </section>

  <section class="card card--back">
    <div class="person">
      <div class="person__name">Daniel Hartwell</div>
      <div class="person__role">Founder</div>
    </div>
    <div class="divider"></div>
    <ul class="contact">
      <li class="contact__item">418 Linden Avenue</li>
      <li class="contact__item">Marlow Falls, WA 99208</li>
      <li class="contact__item">
        <svg class="contact__icon" viewBox="0 0 16 16" aria-hidden="true"><path d="M4 1 L6.5 4.5 L5 6.5 Q7 10 9.5 11 L11.5 9.5 L15 12 L13 15 Q4 14 1 3 Z" fill="none" stroke="#c9c9c9" stroke-width="1.4"/></svg>
        555 013 4470
      </li>
      <li class="contact__item">
        <svg class="contact__icon" viewBox="0 0 16 16" aria-hidden="true"><rect x="1" y="3" width="14" height="10" fill="none" stroke="#c9c9c9" stroke-width="1.4"/><path d="M1 3 L8 9 L15 3" fill="none" stroke="#c9c9c9" stroke-width="1.4"/></svg>
        info@corbelllending.com
      </li>
      <li class="contact__item">
        <svg class="contact__icon" viewBox="0 0 16 16" aria-hidden="true"><circle cx="8" cy="8" r="6.5" fill="none" stroke="#c9c9c9" stroke-width="1.3"/><ellipse cx="8" cy="8" rx="3" ry="6.5" fill="none" stroke="#c9c9c9" stroke-width="1.1"/><path d="M1.5 8 H14.5" stroke="#c9c9c9" stroke-width="1.1"/></svg>
        www.corbelllending.com
      </li>
    </ul>
  </section>
</body>
</html>
```